Business Card Re-Design/Update

We'd like to update out business cards. I've included our current "Style guide" which has the colour scheme of the organisation in it. I've also included the branding files with logos etc in them.

I've also included a copy of one of our existing cards so that you can see how ugly/dated they look. I'd like a fresh modern corporate look.

Target Market(s)

These are for our clients, potential clients, industry contacts - like all business cards

Contact Information for Business Card

Name
Position
Company Address - Level 1, 47 Fernby Street, Carlow Qld 4072
Direct Phone
mobile
Email
Website -www.korvalit.com.au
Logo

Colors

Designer to choose colors to be used in the design.

Requirements
Must have
• Main Logo
• Cards will need to be editable to be able to personalize them for each new employee.
Nice to have
• The MapOut, ShipWell, KeepSteady would be okay to have if they can be sensibly and professionally added to the look without detracting from the main imagery.
• Maybe they could go on the back of the card? will leave this to your creative discretion as to whether/where they fit.
Should not have
• Should not have decorative or script fonts

```html
<!DOCTYPE html>
<html lang="en">
<head>
<meta charset="utf-8">
<title>KorvalIT Business Card</title>
<link rel="stylesheet" href="https://fonts.googleapis.com/css2?family=Arimo:wght@400;700&family=Roboto:wght@400;500&display=swap">
<style>
  :root {
    --canvas: #e6e6e6;
    --card: #f7f7f7;
    --red: #c4161c;
    --red-bright: #d01a21;
    --red-deep: #9c0d12;
    --ink: #1e1e1e;
    --grey-text: #555555;
    --rule: #c9c9c9;
    --black-band: #0b0b0b;
    --white: #ffffff;
  }
  * { margin: 0; padding: 0; box-sizing: border-box; }
  html, body { width: 1200px; height: 960px; overflow: hidden; }
  body { background: var(--canvas); position: relative; font-family: "Arimo", Arial, sans-serif; }

  .card { position: absolute; width: 600px; height: 343px; box-shadow: 0 2px 4px rgba(0,0,0,.25); overflow: hidden; }
  .card-front { left: 314px; top: 113px; background: var(--card); }
  .card-back { left: 311px; top: 472px; background: linear-gradient(180deg, var(--red-bright) 0%, var(--red-deep) 100%); }

  /* front: brand */
  .brand { position: absolute; left: 46px; top: 140px; display: flex; align-items: center; gap: 12px; }
  .brand-square { width: 22px; height: 22px; background: var(--red); }
  .brand-name { font-family: "Roboto", Arial, sans-serif; font-weight: 500; font-size: 30px; color: var(--ink); letter-spacing: -0.5px; }

  .divider { position: absolute; left: 309px; top: 65px; width: 1px; height: 194px; background: var(--rule); }

  /* front: details */
  .details { position: absolute; left: 335px; top: 60px; }
  .person-name { font-weight: 700; font-size: 21px; color: var(--red); line-height: 26px; }
  .person-role { font-size: 14px; color: #111; line-height: 18px; }
  .address { margin-top: 10px; font-size: 14.5px; color: var(--grey-text); line-height: 18px; letter-spacing: .3px; }
  .contacts { list-style: none; margin-top: 10px; }
  .contacts li { display: flex; align-items: center; height: 19px; font-size: 14px; color: var(--grey-text); letter-spacing: .3px; }
  .contacts svg { width: 14px; height: 14px; margin-right: 8px; fill: var(--red); flex: none; }

  /* front: band */
  .web-band { position: absolute; left: 0; top: 299px; width: 600px; height: 30px;
    background: linear-gradient(90deg, var(--red-deep) 0%, var(--red) 40%, var(--red-deep) 62%, var(--black-band) 80%, var(--black-band) 100%); }
  .web-address { position: absolute; left: 116px; top: 7px; font-family: "Roboto", Arial, sans-serif; font-size: 14px; letter-spacing: 3px; color: var(--white); }
  .band-square { position: absolute; left: 446px; top: 3px; width: 24px; height: 24px; background: var(--red); border: 2px solid var(--white); }

  /* back */
  .back-name { position: absolute; left: 0; width: 100%; top: 110px; text-align: center; font-family: "Roboto", Arial, sans-serif; font-weight: 500; font-size: 64px; color: var(--white); letter-spacing: -1px; }
  .services { position: absolute; left: 46px; top: 278px; display: flex; gap: 34px; list-style: none; }
  .services li { display: flex; align-items: center; gap: 8px; font-family: "Roboto", Arial, sans-serif; font-weight: 500; font-size: 25px; color: var(--white); }
  .services .tag-square { width: 16px; height: 16px; background: var(--white); }
</style>
</head>
<body>
  <section class="card card-front" aria-label="Business card front">
    <div class="brand">
      <span class="brand-square"></span>
      <span class="brand-name">KorvalIT</span>
    </div>
    <div class="divider"></div>
    <div class="details">
      <p class="person-name">Maren Holt</p>
      <p class="person-role">Business Development Manager</p>
      <p class="address">22/9 Tallis Creek Road<br>Brayfield QLD 4019</p>
      <ul class="contacts">
        <li><svg viewBox="0 0 16 16" aria-hidden="true"><path d="M3.5 1.5l2.5 0 1 3.5-1.7 1.2c.9 1.9 2.3 3.3 4.2 4.2L10.7 8.7l3.5 1v2.6c0 .8-.7 1.4-1.5 1.3C7 13 3 9 2.2 3.3 2.1 2.2 2.7 1.5 3.5 1.5z"/></svg>+61 (0)7 5550 1420</li>
        <li><svg viewBox="0 0 16 16" aria-hidden="true"><path d="M3.5 1.5l2.5 0 1 3.5-1.7 1.2c.9 1.9 2.3 3.3 4.2 4.2L10.7 8.7l3.5 1v2.6c0 .8-.7 1.4-1.5 1.3C7 13 3 9 2.2 3.3 2.1 2.2 2.7 1.5 3.5 1.5z"/></svg>+61 (0)7 5550 1427</li>
        <li><svg viewBox="0 0 16 16" aria-hidden="true"><path d="M4.5 0h7c.8 0 1.5.7 1.5 1.5v13c0 .8-.7 1.5-1.5 1.5h-7C3.7 16 3 15.3 3 14.5v-13C3 .7 3.7 0 4.5 0zM4.5 2v10.5h7V2zM8 13.3a.9.9 0 100 1.8.9.9 0 000-1.8z"/></svg>+61 (0)400 555 318</li>
        <li><svg viewBox="0 0 16 16" aria-hidden="true"><path d="M4 1h7l1 1v4H4zM1.5 7h13c.6 0 1 .4 1 1v5h-3v-2h-9v2h-3V8c0-.6.4-1 1-1zM4.5 12h7v3h-7z"/></svg>+61 (0)7 5550 1409</li>
        <li><svg viewBox="0 0 16 16" aria-hidden="true"><path d="M1 3h14v1.2L8 8.7 1 4.2zM1 5.6l7 4.5 7-4.5V13H1z"/></svg>mholt@korvalit.com.au</li>
      </ul>
    </div>
    <div class="web-band">
      <span class="web-address">www.korvalit.com.au</span>
      <span class="band-square"></span>
    </div>
  </section>

  <section class="card card-back" aria-label="Business card back">
    <p class="back-name">KorvalIT</p>
    <ul class="services">
      <li><span class="tag-square"></span>MapOut</li>
      <li><span class="tag-square"></span>ShipWell</li>
      <li><span class="tag-square"></span>KeepSteady</li>
    </ul>
  </section>
</body>
</html>
```